Bluefinch Painting needs a Website

We need a website built for a Painting company I own, we mainly do residential painting, but don't want to be limited to that.

Need to have estimate request form.
Need pic's of past projects

I like the look of the website for http://www.harbor-brushworks.com
& "Westlake Home inspections"

My logo that was designed here on ArtHatch on the front page

I would like one of the houses I downloaded as part of the background
of the front page.

Target Market(s)

Home owners

Industry/Entity Type

Painting

Number of Pages Required

1 page

Font styles to use
Serif

Requirements
Must have
• Estimate request form for home owners to fill out -
• Name:
• Phone Number:
• Address:
• E-mail:
• Painting project description:
• And my info to:
• My phone number: (555) 318-7046
• My web address bluefinchpainting.example
Nice to have
• My logo that was designed here on ArtHatch

```html
<!DOCTYPE html>
<html lang="en">
<head>
<meta charset="utf-8">
<title>Bluefinch Painting</title>
<link href="https://fonts.googleapis.com/css2?family=Vollkorn:wght@400;600&family=Roboto:wght@400;500&display=swap" rel="stylesheet">
<style>
:root{
  --blue:#1b7bc8;
  --blue-dark:#1468ad;
  --ink:#222;
  --panel:#f3f3f3;
  --dark:#2b2a28;
  --white:#fff;
  --field:#c9c9c9;
}
*{box-sizing:border-box;margin:0;padding:0}
html,body{width:1188px;height:1200px;overflow:hidden;background:#fff}
body{position:relative;font-family:"Roboto",Arial,sans-serif;color:var(--ink)}
.abs{position:absolute}

.brand{left:158px;top:40px;display:flex;align-items:center;gap:10px}
.brand-mark{width:38px;height:38px;background:var(--blue)}
.brand-name{font-family:"Vollkorn",serif;font-size:31px;color:var(--ink);letter-spacing:1px;line-height:1}

.cta{left:712px;top:17px;width:148px;height:28px;background:var(--blue);color:#fff;font-size:17px;display:flex;align-items:center;justify-content:center;font-weight:500}
.call{left:874px;top:14px;display:flex;gap:8px;align-items:center}
.call small{display:block;font-size:14px}
.call strong{display:block;font-size:19px;font-weight:400}

.nav{left:585px;top:70px;display:flex;gap:20px;font-size:13px;align-items:center}
.nav a{color:var(--ink);text-decoration:none;padding:4px 0}
.nav a.active{background:var(--blue);color:#fff;padding:5px 14px}

.hero{left:0;top:115px;width:1188px;height:393px;background:linear-gradient(180deg,#86aedb 0%,#b9ab90 30%,#8c7e66 60%,#4f6a33 85%,#3c5224 100%)}
.hero h1{left:158px;top:110px;font-family:"Vollkorn",serif;font-weight:400;font-size:30px;line-height:37px;color:#fff;text-shadow:0 2px 4px rgba(0,0,0,.6)}
.arrow{top:177px;width:34px;height:32px;background:rgba(60,60,60,.85);display:flex;align-items:center;justify-content:center}
.tab{top:348px;height:45px;padding:0 12px;display:flex;align-items:center;font-family:"Vollkorn",serif;font-size:20px;color:#fff}
.tab.res{left:158px;background:var(--blue);font-weight:600}
.tab.com{left:428px;background:var(--dark)}

.gallery{left:158px;top:508px;width:873px;height:213px;background:linear-gradient(180deg,#fff,var(--panel))}
.filter{left:20px;top:18px;font-family:"Vollkorn",serif;font-size:20px}
.filter .on{color:var(--blue);border-left:1px solid var(--blue);padding-left:9px;margin-left:6px}
.thumb{top:60px;width:153px;height:122px;border:1px solid #444;padding:4px;background:#fff}
.thumb div{position:relative;width:100%;height:100%;background:linear-gradient(160deg,#7ea5d4,#a79b84 50%,#5c7a3c)}
.thumb span{position:absolute;left:0;right:0;bottom:0;height:23px;background:rgba(40,40,40,.7);color:#fff;font-family:"Vollkorn",serif;font-size:16px;padding:1px 8px}

.about{left:0;top:766px;width:1188px;height:366px;background:linear-gradient(180deg,#2f302e,#3a3935 60%,#2a2a28)}
.about h2{font-family:"Vollkorn",serif;font-weight:400;font-size:22px;color:#fff}
.rule{height:3px;border-top:1px solid #fff;border-bottom:1px solid #fff;margin-top:10px}
.welcome{left:160px;top:24px;width:342px}
.copy{left:160px;top:80px;width:510px;color:#fff;font-size:12.5px;line-height:22px}
.btn{border:2px solid #ddd;border-radius:4px;color:#fff;font-size:13px;font-weight:500;padding:5px 10px}
.more{left:157px;top:288px}
.estimate{left:729px;top:22px;width:302px}
.form{left:729px;top:85px;width:262px}
.field{height:29px;background:var(--field);margin-bottom:10px;font-size:13px;padding:6px 12px;color:#333}
.field.area{height:76px}
.submit{left:729px;top:288px;padding:5px 24px}

.footer{left:0;top:1132px;width:1188px;height:68px;background:var(--blue);color:#fff}
.footer nav{left:163px;top:15px;display:flex;gap:18px;font-size:13px}
.footer p{left:160px;top:38px;font-size:12px}
.footer .brand{left:810px;top:16px}
.footer .brand-mark{width:28px;height:28px;background:#fff}
.footer .brand-name{font-size:23px;color:#fff}
</style>
</head>
<body>

<div class="abs brand"><span class="brand-mark"></span><span class="brand-name">BLUEFINCH PAINTING</span></div>
<div class="abs cta">Free Estimates</div>
<div class="abs call">
  <svg width="28" height="28" viewBox="0 0 28 28"><circle cx="14" cy="14" r="12" fill="none" stroke="#1b7bc8" stroke-width="2"/><path d="M10 8c-2 3 0 9 5 12l2-2-3-3-1 1c-1-1-2-3-2-5l1-1-2-3z" fill="#1b7bc8"/></svg>
  <div><small>Call Us Today</small><strong>555-318-7046</strong></div>
</div>
<nav class="abs nav">
  <a class="active" href="#">HOME</a><a href="#">ABOUT US</a><a href="#">SERVICES</a><a href="#">PAST PROJECTS</a><a href="#">CONTACT US</a>
</nav>

<section class="abs hero" role="img" aria-label="Photo of a freshly painted two-storey house with flowering shrubs">
  <h1 class="abs">PROVIDING QUALITY WORK AT<br>AFFORDABLE PRICES</h1>
  <div class="abs arrow" style="left:6px"><svg width="10" height="14"><path d="M8 2 3 7l5 5" stroke="#fff" stroke-width="2.5" fill="none"/></svg></div>
  <div class="abs arrow" style="left:1146px"><svg width="10" height="14"><path d="M2 2l5 5-5 5" stroke="#fff" stroke-width="2.5" fill="none"/></svg></div>
  <div class="abs tab res">RESIDENTIAL PAINTING</div>
  <div class="abs tab com">COMMERCIAL PAINTING</div>
</section>

<section class="abs gallery">
  <div class="abs filter">Interior <span class="on">Exterior</span></div>
  <div class="abs thumb" style="left:15px"><div role="img" aria-label="Painted house exterior"><span>Lorem Ispum</span></div></div>
  <div class="abs thumb" style="left:186px"><div role="img" aria-label="Painter working on siding gable"><span>Lorem Ispum</span></div></div>
  <div class="abs thumb" style="left:357px"><div role="img" aria-label="Painter spraying a wall"><span>Lorem Ispum</span></div></div>
  <div class="abs thumb" style="left:528px"><div role="img" aria-label="Painted home with lawn"><span>Lorem Ispum</span></div></div>
  <div class="abs thumb" style="left:699px"><div role="img" aria-label="Painted two-storey home with patio"><span>Lorem Ispum</span></div></div>
</section>

<section class="abs about" role="img" aria-label="Dimmed photo of company work trucks in front of a house">
  <div class="abs welcome"><h2>Welcome to Bluefinch Painting</h2><div class="rule"></div></div>
  <p class="abs copy">Lorem ipsum dolor sit amet, consectetuer adipiscing elit, sed diam nonummy nibh euismod consequat. Duis autem revel eum iriure dolor in hendrerit in vulputate velit esse molestie consequat.Lorem ipsum dolor sit amet, consectetuer adipiscing elit, sed diam nonummy nibh euismod rent ut laoreet dolore magna aliquam erat volutpat. Ut wisi enim ad minim veniam, quis nostrud lore xererci tation ullamcorper suscipit lobortis nisl ut aliquip ex ea commodo consequat. Duis autem revel eum iriure dolor in hendrerit in vulputate velit esse molestie consequat.nibh euismod rent ut laoreet dolore magna aliquam erat volutpat. Ut wisi enim ad minim veniam, quis nostrud lore xererci tation ullamcorper suscipit lobortis nisl ut aliquip ex ea commodo consequat.</p>
  <div class="abs btn more">Read More</div>
  <div class="abs estimate"><h2>Free Painting Estimates</h2><div class="rule"></div></div>
  <div class="abs form">
    <div class="field">Name</div>
    <div class="field">Email</div>
    <div class="field">Phone</div>
    <div class="field area">Painting project description</div>
  </div>
  <div class="abs btn submit">Submit</div>
</section>

<footer class="abs footer">
  <nav class="abs"><span>• Home</span><span>• About Us</span><span>• Services</span><span>• Past Projects</span><span>• Contact Us</span></nav>
  <p class="abs">Copyright ©2015, BluefinchPainting&nbsp; All Rights Reserved</p>
  <div class="abs brand"><span class="brand-mark"></span><span class="brand-name">BLUEFINCH PAINTING</span></div>
</footer>

</body>
</html>
```